Android Payment Application UI Design

We require a UI/UX design for an existing Android card-based payment application.

We're looking to improve the look + feel of the existing app. What we're after:
- Colour palette options
- Fonts
- Icons

See attached document for existing screen types, icons, etc.

All resources provided must be royalty free.

It's to run on a specialised device, with 720 x 1280 pixel resolution, in portrait only (landscape not required).

Please provide mockup examples of the new screen layout applied to the existing screens in the document.

Target Market(s)

Retail business users

Font styles to use
Sans Serif

Colors

Designer to choose colors to be used in the design.

Requirements
Must have
• Looking for
• - modern design
• - simple colours, easy-to-read sans-serif fonts
• - cohesive, consistent design between screens

```html
<!DOCTYPE html>
<html lang="en">
<head>
<meta charset="utf-8">
<title>Main Menu</title>
<link href="https://fonts.googleapis.com/css2?family=Open+Sans:wght@400;600;700&display=swap" rel="stylesheet">
<style>
  :root {
    --white: #ffffff;
    --ink: #1c1c1c;
    --icon: #3a3a3a;
    --band-top: #0b2350;
    --band-bottom: #1b5d9e;
    --sky-top: #ffffff;
    --sky-bottom: #6fc1ea;
    --card-border: #d6dde4;
    --card-text: #555d66;
    --drop-bg: #1f8fd0;
    --drop-line: #4aa9de;
    --brand: #2a4f86;
    --battery: #e0332c;
  }
  * { box-sizing: border-box; margin: 0; padding: 0; }
  html, body { width: 675px; height: 1200px; overflow: hidden; }
  body { font-family: "Open Sans", Arial, sans-serif; background: var(--white); }
  .screen {
    position: relative; width: 675px; height: 1200px; overflow: hidden;
    background: linear-gradient(180deg, var(--sky-top) 0%, var(--sky-top) 28%, #d9eef9 62%, var(--sky-bottom) 100%);
  }
  .status-bar {
    position: absolute; left: 0; top: 0; width: 675px; height: 38px;
    background: var(--white); color: var(--ink); font-size: 18px;
    display: flex; align-items: center; padding: 0 14px;
  }
  .status-left { display: flex; align-items: center; gap: 6px; }
  .status-time { position: absolute; left: 0; right: 0; text-align: center; }
  .status-right { margin-left: auto; display: flex; align-items: center; gap: 8px; }
  .app-header {
    position: absolute; left: 0; top: 38px; width: 675px; height: 124px;
    background: radial-gradient(ellipse at 50% 40%, #ffffff 40%, #eef4f9 100%);
  }
  .header-icon { position: absolute; top: 62px; }
  .header-icon.db { left: 14px; }
  .header-icon.menu { right: 20px; }
  .brand {
    position: absolute; left: 0; right: 0; top: 40px;
    display: flex; justify-content: center; align-items: center; gap: 14px;
  }
  .brand-dot { width: 40px; height: 40px; border-radius: 50%; background: var(--brand); }
  .brand-name { font-size: 42px; font-weight: 700; color: var(--brand); letter-spacing: 2px; line-height: 1; }
  .title-band {
    position: absolute; left: 0; top: 162px; width: 675px; height: 142px;
    background: linear-gradient(170deg, var(--band-top) 0%, #123a72 55%, var(--band-bottom) 100%);
  }
  .title-band h1 {
    position: absolute; left: 99px; top: 56px;
    color: var(--white); font-size: 27px; font-weight: 400;
  }
  .menu-list { position: absolute; left: 83px; top: 338px; width: 511px; list-style: none; }
  .menu-item {
    height: 88px; margin-bottom: 25px; background: var(--white);
    border: 1px solid var(--card-border); border-radius: 12px;
    display: flex; align-items: center; padding-left: 36px;
    font-size: 17px; color: var(--card-text);
    box-shadow: 0 1px 3px rgba(0,0,0,0.05);
  }
  .dropdown {
    position: absolute; left: 421px; top: 180px; width: 234px;
    background: var(--drop-bg); list-style: none;
    box-shadow: 0 3px 8px rgba(0,0,0,0.2);
  }
  .dropdown li {
    height: 57px; display: flex; align-items: center; padding-left: 28px;
    color: var(--white); font-size: 17px; border-bottom: 1px solid var(--drop-line);
  }
  .dropdown li:last-child { border-bottom: none; }
</style>
</head>
<body>
<div class="screen">
  <div class="status-bar">
    <div class="status-left">
      <svg width="52" height="12" viewBox="0 0 52 12" aria-hidden="true">
        <circle cx="6" cy="6" r="5" fill="#1c1c1c"/><circle cx="16" cy="6" r="5" fill="#1c1c1c"/>
        <circle cx="26" cy="6" r="5" fill="#1c1c1c"/><circle cx="36" cy="6" r="5" fill="#1c1c1c"/>
        <circle cx="46" cy="6" r="4.5" fill="none" stroke="#1c1c1c"/>
      </svg>
      <span>Carrier</span>
    </div>
    <div class="status-time">11:49 AM</div>
    <div class="status-right">
      <span>2%</span>
      <svg width="46" height="20" viewBox="0 0 46 20" aria-hidden="true">
        <rect x="1" y="1" width="40" height="18" rx="4" fill="none" stroke="#1c1c1c" stroke-width="2"/>
        <rect x="42" y="6" width="3" height="8" rx="1" fill="#1c1c1c"/>
        <rect x="4" y="4" width="4" height="12" rx="1" fill="var(--battery)"/>
      </svg>
    </div>
  </div>

  <header class="app-header">
    <svg class="header-icon db" width="22" height="34" viewBox="0 0 22 34" aria-label="Data">
      <ellipse cx="11" cy="5" rx="10" ry="4" fill="var(--icon)"/>
      <path d="M1 9 Q11 15 21 9 V15 Q11 21 1 15Z" fill="var(--icon)"/>
      <path d="M1 18 Q11 24 21 18 V24 Q11 30 1 24Z" fill="var(--icon)"/>
      <path d="M1 27 Q11 33 21 27 V29 Q11 35 1 29Z" fill="var(--icon)"/>
    </svg>
    <div class="brand">
      <span class="brand-dot"></span>
      <span class="brand-name">VELNOR</span>
    </div>
    <svg class="header-icon menu" width="30" height="26" viewBox="0 0 30 26" aria-label="Menu">
      <rect x="0" y="1" width="5" height="4" fill="var(--icon)"/><rect x="8" y="1" width="22" height="4" fill="var(--icon)"/>
      <rect x="0" y="11" width="5" height="4" fill="var(--icon)"/><rect x="8" y="11" width="22" height="4" fill="var(--icon)"/>
      <rect x="0" y="21" width="5" height="4" fill="var(--icon)"/><rect x="8" y="21" width="22" height="4" fill="var(--icon)"/>
    </svg>
  </header>

  <section class="title-band">
    <h1>Main Menu</h1>
  </section>

  <ul class="menu-list">
    <li class="menu-item">Sale</li>
    <li class="menu-item">Reversal</li>
    <li class="menu-item">Refund</li>
    <li class="menu-item">Pre-auth</li>
    <li class="menu-item">Completion</li>
    <li class="menu-item">Reconciliation</li>
    <li class="menu-item">Print manager</li>
  </ul>

  <ul class="dropdown">
    <li>Logout</li>
    <li>Settings</li>
    <li>Wifi Settings</li>
    <li>Data Settings</li>
    <li>Input Settings</li>
    <li>App Settings</li>
  </ul>
</div>
</body>
</html>
```